Business Card Design for Training Business

Clear Path Coaching is a new business that delivers training and other services with a focus on topics related to mental health and wellbeing, for example, Wellmind Response Course, Resilience etc. We have a strong focus on evidence-based psychology and neuroscience. I have a logo which I will upload with the brief, so please consider colours that work well with the logo.
Target Market(s)
Adults, workplaces (particularly government and not-for-profits)
Industry/Entity Type
Business
Contact Information for Business Card
Head Strong TrainingSamantha SellwoodDirector0438 770 850sam@headstrongtraining.com.auwww.headstrongtraining.com.au

```html
<!DOCTYPE html>
<html lang="en">
<head>
<meta charset="utf-8">
<title>Clear Path Coaching – Business Card</title>
<link href="https://fonts.googleapis.com/css2?family=Questrial&display=swap" rel="stylesheet">
<style>
  :root {
    --backdrop: #3b3b3b;
    --teal: #22b8bd;
    --teal-soft: #6fd3d3;
    --paper: #f7f7f7;
    --ink-white: #ffffff;
    --ink-grey: #6b6b6b;
  }
  * { box-sizing: border-box; margin: 0; padding: 0; }
  html, body {
    width: 1200px; height: 750px; overflow: hidden;
    background: var(--backdrop);
    font-family: "Questrial", "Century Gothic", sans-serif;
  }
  .canvas {
    position: relative; width: 1200px; height: 750px;
    display: flex; justify-content: center; align-items: center; gap: 8px;
  }
  .card {
    position: relative; width: 540px; height: 308px; overflow: hidden;
  }
  .card--front { background: var(--teal); color: var(--ink-white); }
  .card--back { background: var(--paper); }

  .front__wordmark {
    position: absolute; left: 47px; top: 60px;
    font-size: 22px; letter-spacing: 3px; text-transform: uppercase;
    color: var(--ink-white);
  }
  .front__name {
    position: absolute; left: 47px; top: 138px;
    font-size: 22px;
  }
  .front__role {
    position: absolute; left: 47px; top: 165px;
    font-size: 16px;
  }
  .front__contacts {
    position: absolute; left: 47px; top: 198px;
    list-style: none; font-size: 14px; line-height: 21px;
  }
  .front__contacts li { display: flex; align-items: center; gap: 7px; }
  .front__contacts svg { width: 14px; height: 14px; flex: none; }

  .front__decor {
    position: absolute; right: 0; top: 0; width: 160px; height: 308px;
    background: linear-gradient(90deg, rgba(255,255,255,0) 0%, rgba(255,255,255,0.12) 60%, rgba(255,255,255,0.28) 100%);
  }
  .back__decor {
    position: absolute; left: 0; top: 0; width: 160px; height: 308px;
    background: linear-gradient(90deg, rgba(34,184,189,0.35) 0%, rgba(111,211,211,0.15) 55%, rgba(247,247,247,0) 100%);
  }

  .back__logo {
    position: absolute; left: 348px; top: 92px; transform: translateX(-50%);
    display: flex; flex-direction: column; align-items: center; gap: 22px;
  }
  .back__dot {
    width: 72px; height: 72px; border-radius: 50%;
    background: radial-gradient(circle, #ffffff 0%, var(--teal-soft) 70%, var(--teal) 100%);
  }
  .back__name {
    font-size: 19px; letter-spacing: 2.5px; text-transform: uppercase;
    color: var(--ink-grey); white-space: nowrap;
  }
</style>
</head>
<body>
<main class="canvas">
  <section class="card card--front">
    <div class="front__wordmark">Clear Path Coaching</div>
    <div class="front__name">Rebecca Tanfield</div>
    <div class="front__role">Director</div>
    <ul class="front__contacts">
      <li>
        <svg viewBox="0 0 16 16" aria-hidden="true"><path fill="#fff" d="M3.5 1.5l2.2 2.6-1.2 1.8c.9 2 2.5 3.6 4.6 4.6l1.8-1.2 2.6 2.2-1.3 2.2C7.6 15.2.8 8.4 1.3 2.8z"/></svg>
        <span>0491 362 517</span>
      </li>
      <li>
        <svg viewBox="0 0 16 16" aria-hidden="true"><rect x="1" y="3.5" width="14" height="9.5" fill="#fff"/><path d="M1.5 4l6.5 5 6.5-5" fill="none" stroke="#22b8bd" stroke-width="1.3"/></svg>
        <span>bec@clearpathcoaching.example.au</span>
      </li>
      <li>
        <svg viewBox="0 0 16 16" aria-hidden="true"><circle cx="8" cy="8" r="7" fill="#fff"/><path d="M1.5 8h13M8 1c-3 3.5-3 10.5 0 14M8 1c3 3.5 3 10.5 0 14" fill="none" stroke="#22b8bd" stroke-width="1.1"/></svg>
        <span>www.clearpathcoaching.example.au</span>
      </li>
    </ul>
    <div class="front__decor" role="img" aria-label="Large brand symbol decoration in white line work"></div>
  </section>

  <section class="card card--back">
    <div class="back__decor" role="img" aria-label="Large brand symbol decoration in teal line work fading to white"></div>
    <div class="back__logo">
      <div class="back__dot"></div>
      <div class="back__name">Clear Path Coaching</div>
    </div>
  </section>
</main>
</body>
</html>
```